4th Generation Family Business Needs a New Card Design!

We are a family owned 4th Generation company. We are based in the Sydney, Australia area and we are desperately in need of a more modern and classy card. We are monumental masons who design, supply & erect lasting memorials throughout cemeteries in Sydney. Our customers are normally in a period of grieving. I have attached logo files that will need to be implemented on the card. Company was established 1935. Australian Owned and Operated. Card needs to be designed to PIXO.com specification.

Target Market(s)

Our target market is based upon people that a grieving for family members that have passed away. We also deal with alot of companies that own and operate cemeteries.

Industry/Entity Type

Business

Contact Information for Business Card

Simon Harcourt, Operations Manager, 0417293086, simon@harcourtmemorials.com.au
Lewis Harcourt, Director, 0491630572, lewis@harcourtmemorials.com.au
Phone # 02 9561 3048
Website: www.harcourtmemorials.com.au
Address: Suite 17, 8 Palfrey Lane, West Carlow, Sydney NSW 2156

Font styles to use
Serif
Decorative
Script

Requirements
Must have
• Would like to see the logo nicely implemented with a modern design. Embossed lettering would be a nice additive.

```html
<!DOCTYPE html>
<html lang="en">
<head>
<meta charset="utf-8">
<title>Harcourt Memorials – Business Card</title>
<link href="https://fonts.googleapis.com/css2?family=Cinzel:wght@500&family=Source+Sans+3:wght@400;600&display=swap" rel="stylesheet">
<style>
  :root {
    --bg-top: #2a2a2a;
    --bg-bottom: #050505;
    --card: #ffffff;
    --ink: #1a1a1a;
    --gold: #e8b818;
  }
  * { margin: 0; padding: 0; box-sizing: border-box; }
  html, body { width: 1200px; height: 900px; overflow: hidden; }
  body {
    background: linear-gradient(180deg, var(--bg-top) 0%, #161616 45%, var(--bg-bottom) 100%);
    font-family: "Source Sans 3", "Myriad Pro", sans-serif;
    color: var(--ink);
    position: relative;
  }
  .card {
    position: absolute;
    top: 306px;
    width: 440px;
    height: 271px;
    background: var(--card);
    border-radius: 10px;
  }
  .card--front { left: 149px; }
  .card--back { left: 608px; }

  .wordmark {
    position: absolute;
    left: 0; right: 0;
    text-align: center;
    font-family: "Cinzel", serif;
    font-weight: 500;
    color: var(--ink);
    line-height: 1;
  }
  .card--front .wordmark { top: 26px; font-size: 40px; letter-spacing: 0.5px; }
  .card--front .wordmark-sub { top: 68px; font-size: 22px; }

  .contacts {
    position: absolute;
    top: 110px;
    left: 0; right: 0;
    display: flex;
    justify-content: center;
    gap: 21px;
    font-size: 12.5px;
  }
  .person { display: flex; flex-direction: column; }
  .person--left { align-items: flex-end; text-align: right; }
  .person--right { align-items: flex-start; text-align: left; }
  .person-name { color: var(--gold); font-weight: 600; font-size: 15.5px; line-height: 18px; }
  .person-role { line-height: 15px; }
  .person-line { display: flex; align-items: center; gap: 5px; line-height: 16px; }
  .person-phone { margin-top: 9px; }
  .icon { width: 9px; height: 9px; fill: var(--gold); flex: none; }

  .company-info {
    position: absolute;
    top: 200px;
    left: 0; right: 0;
    text-align: center;
    font-size: 12.5px;
    line-height: 16px;
  }
  .company-web { color: var(--gold); }
  .company-address { margin-top: 7px; }

  .brand-block {
    position: absolute;
    left: 0; right: 0;
    top: 96px;
    display: flex;
    flex-direction: column;
    align-items: center;
    gap: 12px;
  }
  .brand-mark { width: 22px; height: 22px; background: var(--gold); }
  .card--back .wordmark { position: static; font-size: 36px; }
  .card--back .wordmark-sub { font-size: 20px; margin-top: -6px; }
</style>
</head>
<body>
  <section class="card card--front" aria-label="Card front">
    <div class="wordmark">Harcourt Memorials</div>

    <div class="contacts">
      <div class="person person--left">
        <span class="person-name">Lewis Harcourt</span>
        <span class="person-role">Director</span>
        <span class="person-line person-phone">0491630572
          <svg class="icon" viewBox="0 0 10 10" aria-hidden="true"><path d="M2 0.5 3.6 2.6 2.7 3.6C3.3 5 4.9 6.6 6.4 7.3L7.4 6.4 9.5 8 8.4 9.5C4.5 9.2 0.8 5.5 0.5 1.6Z"/></svg>
        </span>
        <span class="person-line">lewis@harcourtmemorials.com.au
          <svg class="icon" viewBox="0 0 10 10" aria-hidden="true"><path d="M0.5 2h9v6h-9z M0.5 2 5 5.5 9.5 2" fill="var(--gold)" stroke="#fff" stroke-width="0.8"/></svg>
        </span>
      </div>
      <div class="person person--right">
        <span class="person-name">Simon Harcourt</span>
        <span class="person-role">Operations Manager</span>
        <span class="person-line person-phone">
          <svg class="icon" viewBox="0 0 10 10" aria-hidden="true"><path d="M2 0.5 3.6 2.6 2.7 3.6C3.3 5 4.9 6.6 6.4 7.3L7.4 6.4 9.5 8 8.4 9.5C4.5 9.2 0.8 5.5 0.5 1.6Z"/></svg>0417293086
        </span>
        <span class="person-line">
          <svg class="icon" viewBox="0 0 10 10" aria-hidden="true"><path d="M0.5 2h9v6h-9z M0.5 2 5 5.5 9.5 2" fill="var(--gold)" stroke="#fff" stroke-width="0.8"/></svg>simon@harcourtmemorials.com.au
        </span>
      </div>
    </div>

    <div class="company-info">
      <p class="company-phone"># 02 9561 3048</p>
      <p class="company-web">www.harcourtmemorials.com.au</p>
      <p class="company-address">Suite 17, 8 Palfrey Lane, West Carlow, Sydney NSW 2156</p>
    </div>
  </section>

  <section class="card card--back" aria-label="Card back">
    <div class="brand-block">
      <span class="brand-mark" aria-hidden="true"></span>
      <div class="wordmark">Harcourt Memorials</div>
    </div>
  </section>
</body>
</html>
```